Kettle Ridge Kitchen Hour Podcast Episode Cover

I’m looking for a clean, professional, and eye-catching podcast episode cover template for my show, Kettle Ridge Kitchen Hour. Each week, I feature a new guest, so the design must allow me (or my team) to easily swap in a new guest’s photo without needing advanced design skills.

The template should be:

- Drag-and-drop friendly: simple for me to replace the guest’s headshot in Canva, Photoshop, or similar.
- On-brand with the Kettle Ridge Kitchen Hour podcast: professional yet approachable, foodservice industry-focused.
- Bold and attention-grabbing for podcast platforms and social media.

Readable text at small sizes, since covers are often viewed as thumbnails.

Design Elements to Include:

1. Podcast Title: “Kettle Ridge Kitchen Hour” (prominently displayed)
2. Subtitle/Space: Line for guest’s name, professional title, and company name
3. Photo Placeholder: Large, central area where I can easily drag and drop a guest photo
4. Brand Colors: attached
5. Clean, modern fonts (easy to read at thumbnail size)
6. Background graphics or patterns that give a sense of foodservice, leadership, or nationwide reach... but do not overpower the guest photo

Format Requirements:

- Editable source file (PSD, Canva template, or layered AI/INDD)
- JPG/PNG exports for immediate use
- Square format (3000x3000px) for podcast platforms

Style Inspiration:
Think modern podcast covers: bold fonts, clean lines, professional with a touch of energy.

Deliverables:

1. Final episode cover template (editable file)
2. Instructions or guidance on how to swap out guest photos

```html
<!DOCTYPE html>
<html lang="en">
<head>
<meta charset="UTF-8">
<title>Kettle Ridge Kitchen Hour – Episode Cover</title>
<link rel="stylesheet" href="https://fonts.googleapis.com/css2?family=Bebas+Neue&family=Montserrat:wght@400;700&display=swap">
<style>
  :root {
    --navy: #1d3a4f;
    --navy-deep: #1a3447;
    --gold: #fbb817;
    --white: #ffffff;
    --suit-light: #8a8c8f;
    --suit-dark: #5d5f63;
  }
  * { margin: 0; padding: 0; box-sizing: border-box; }
  html, body { width: 1200px; height: 1200px; overflow: hidden; background: var(--navy); }
  .cover {
    position: relative;
    width: 1200px;
    height: 1200px;
    overflow: hidden;
    background:
      radial-gradient(ellipse 300px 380px at 850px 640px, rgba(251,184,23,0.75) 0%, rgba(251,184,23,0.35) 45%, rgba(29,58,79,0) 100%),
      var(--navy);
  }
  .frame-top {
    position: absolute; left: 0; top: 0; width: 1200px; height: 7px;
    background: linear-gradient(90deg, var(--gold) 70%, rgba(251,184,23,0.3) 100%);
  }
  .frame-left {
    position: absolute; left: 0; top: 0; width: 7px; height: 1200px;
    background: linear-gradient(180deg, var(--gold) 55%, rgba(251,184,23,0) 100%);
  }
  .show-title {
    position: absolute; left: 60px; top: 78px; width: 600px;
    font-family: "Bebas Neue", sans-serif;
    font-size: 128px; line-height: 140px; letter-spacing: 1px;
    color: var(--gold);
    text-transform: uppercase;
  }
  .guest-name {
    position: absolute; left: 53px; top: 418px;
    font-family: "Montserrat", sans-serif; font-weight: 700;
    font-size: 108px; line-height: 136px;
    color: var(--white); text-transform: uppercase;
  }
  .guest-photo {
    position: absolute; left: 475px; top: 93px; width: 670px; height: 1107px;
  }
  .info-row {
    position: absolute; left: 67px; display: flex; align-items: center; gap: 35px;
  }
  .info-row.profession { top: 721px; }
  .info-row.company { top: 856px; }
  .info-icon {
    width: 86px; height: 86px; border-radius: 50%;
    background: var(--gold);
    display: flex; align-items: center; justify-content: center;
    flex-shrink: 0;
  }
  .info-label {
    font-family: "Montserrat", sans-serif; font-weight: 700;
    font-size: 22px; color: var(--gold); text-transform: uppercase;
    margin-bottom: 10px;
  }
  .info-value {
    font-family: "Montserrat", sans-serif; font-weight: 400;
    font-size: 26px; color: var(--white);
  }
</style>
</head>
<body>
<main class="cover">
  <div class="frame-top"></div>
  <div class="frame-left"></div>

  <h1 class="show-title">Kettle Ridge<br>Kitchen Hour</h1>

  <h2 class="guest-name">Marcus<br>Hale</h2>

  <svg class="guest-photo" viewBox="0 0 670 1107" role="img" aria-label="Guest headshot: smiling man in a grey suit and white shirt, arms crossed">
    <defs>
      <linearGradient id="photoTone" x1="0" y1="0" x2="0" y2="1">
        <stop offset="0" stop-color="#9a9c9f"/>
        <stop offset="0.45" stop-color="var(--suit-light)"/>
        <stop offset="1" stop-color="var(--suit-dark)"/>
      </linearGradient>
    </defs>
    <path d="M210 0 H430 Q470 0 470 60 V320 Q470 340 520 360 L640 410 Q670 425 670 470 V1107 H90 L0 800 Q0 640 60 460 Q80 410 130 395 L180 370 Q200 350 200 320 V60 Q200 0 210 0 Z" fill="url(#photoTone)"/>
  </svg>

  <div class="info-row profession">
    <div class="info-icon">
      <svg width="44" height="40" viewBox="0 0 44 40" fill="none" stroke="#fff" stroke-width="2.4" stroke-linejoin="round">
        <rect x="2" y="10" width="40" height="28" rx="3"/>
        <path d="M15 10 V5 Q15 3 17 3 H27 Q29 3 29 5 V10"/>
        <path d="M2 22 H18 M26 22 H42"/>
        <rect x="18" y="19" width="8" height="6" rx="1"/>
      </svg>
    </div>
    <div class="info-text">
      <p class="info-label">Profession</p>
      <p class="info-value">Foodservice Division</p>
    </div>
  </div>

  <div class="info-row company">
    <div class="info-icon">
      <svg width="50" height="50" viewBox="0 0 50 50" fill="none" stroke="#fff" stroke-width="2.4" stroke-linejoin="round">
        <path d="M4 47 V4 L28 9 V47"/>
        <path d="M28 20 L46 25 V47"/>
        <path d="M2 47 H48"/>
        <path d="M10 15 H14 M18 15 H22 M10 22 H14 M18 22 H22 M10 29 H14 M18 29 H22 M34 31 H40 M34 37 H40"/>
        <rect x="11" y="36" width="9" height="11"/>
      </svg>
    </div>
    <div class="info-text">
      <p class="info-label">Company Name</p>
      <p class="info-value">Brightwell Beverages</p>
    </div>
  </div>
</main>
</body>
</html>
```